Zolvana Stationary and Branding Documents

Corporate Identity Branding stationary needed for IT Recruiting Firm.

I already have a Logo, business cards and website. I need to get designs completed for the remaining corporate identity documents.

The documentation should use similar colors as my website and business card. The designs should modern and clean.

http://zolvanaworks.example/

Target Market(s)

Information Technology Industry

Industry/Entity Type

Information Technology

Colors
3377b5
0255a3
fbee3e
f78f20
f37122
33a6d7
000000
0592cd

Requirements
Must have
• Letter Head
• Folder Design
• PowerPoint Design
• Invoice
• Envelope
Nice to have
• Proposal
• Flyer
• Brochure
Should not have
• Logo
• Business Cards
• Website

```html
<!DOCTYPE html>
<html lang="en">
<head>
<meta charset="utf-8">
<title>Zolvana Envelope</title>
<link rel="stylesheet" href="https://fonts.googleapis.com/css2?family=Open+Sans:wght@400;600;700&display=swap">
<style>
  :root {
    --backdrop: #2f5580;
    --paper: #f4f4f4;
    --paper-shade: #ececec;
    --fold-line: #dedede;
    --brand-blue: #3377b5;
    --deep-blue: #0255a3;
    --flap-light: #3f80bd;
    --flap-dark: #2a68a8;
    --brand-orange: #f37122;
    --soft-orange: #f78f20;
    --wash-blue: #e3eaf0;
    --wash-sand: #f1e4d7;
    --text-grey: #6d6d6d;
  }
  * { margin: 0; padding: 0; box-sizing: border-box; }
  html, body { width: 1200px; height: 950px; overflow: hidden; }
  body {
    background: var(--backdrop);
    font-family: "Open Sans", Arial, sans-serif;
    position: relative;
  }

  .envelope {
    position: absolute;
    width: 620px;
    height: 310px;
    background: var(--paper);
    overflow: hidden;
  }
  .envelope-front { left: 60px; top: 80px; }
  .envelope-back { left: 520px; top: 500px; }

  /* front */
  .decor-wash {
    position: absolute;
    inset: 0;
    background: linear-gradient(160deg,
      rgba(244,244,244,0) 45%,
      var(--wash-blue) 62%,
      var(--wash-sand) 80%);
  }
  .footer-band {
    position: absolute;
    left: 0;
    bottom: 0;
    width: 100%;
    height: 14px;
    display: flex;
  }
  .footer-band .band-orange { flex: 1; background: var(--brand-orange); }
  .footer-band .band-blue { width: 60px; background: var(--brand-blue); }

  .corner-bars { position: absolute; display: flex; flex-direction: column; gap: 4px; }
  .corner-bars span { display: block; width: 6px; height: 26px; }
  .corner-bars .bar-orange { background: var(--brand-orange); }
  .corner-bars .bar-blue { background: var(--brand-blue); }
  .corner-left { left: 0; top: 118px; }
  .corner-right { right: 0; top: 0; }

  .brand {
    position: absolute;
    left: 40px;
    top: 118px;
    display: flex;
    align-items: center;
    gap: 10px;
  }
  .brand-mark { width: 12px; height: 12px; background: var(--brand-orange); }
  .brand-name {
    font-size: 44px;
    font-weight: 400;
    color: var(--brand-blue);
    letter-spacing: 1px;
    line-height: 1;
  }

  .contact {
    position: absolute;
    left: 150px;
    bottom: 24px;
    font-size: 10px;
    line-height: 1.45;
    color: var(--text-grey);
  }
  .contact li { list-style: none; display: flex; align-items: center; gap: 5px; white-space: nowrap; }
  .contact .address { color: var(--deep-blue); font-weight: 700; }
  .contact svg { width: 9px; height: 9px; flex: none; }

  /* back */
  .envelope-back svg.folds { position: absolute; inset: 0; }
  .flap-pattern {
    position: absolute;
    left: 0;
    top: 0;
    width: 620px;
    height: 112px;
    background: linear-gradient(100deg, var(--flap-dark), var(--flap-light) 50%, var(--flap-dark));
    clip-path: path("M0 0 H620 V60 Q620 70 600 72 L420 100 Q310 116 200 100 L20 72 Q0 70 0 60 Z");
  }
  .back-mark {
    position: absolute;
    right: 150px;
    bottom: 70px;
    width: 28px;
    height: 28px;
    border-radius: 4px;
    background: var(--soft-orange);
  }
</style>
</head>
<body>

<section class="envelope envelope-front" aria-label="Envelope front">
  <div class="decor-wash" role="img" aria-label="Soft blue and sand swoosh decoration"></div>
  <div class="footer-band"><span class="band-orange"></span><span class="band-blue"></span></div>

  <div class="corner-bars corner-left">
    <span class="bar-orange"></span>
    <span class="bar-blue"></span>
  </div>
  <div class="corner-bars corner-right">
    <span class="bar-orange"></span>
    <span class="bar-blue"></span>
  </div>

  <div class="brand">
    <span class="brand-mark"></span>
    <span class="brand-name">Zolvana</span>
  </div>

  <ul class="contact">
    <li class="address">
      <svg viewBox="0 0 10 10"><path d="M5 0.5a3 3 0 0 1 3 3c0 2.3-3 6-3 6s-3-3.7-3-6a3 3 0 0 1 3-3z" fill="var(--deep-blue)"/><circle cx="5" cy="3.5" r="1.1" fill="#fff"/></svg>
      Two Harbor Plaza 410 8th Avenue
    </li>
    <li>
      <svg viewBox="0 0 10 10"><path d="M2 1l2 2-1 1.2c.6 1.3 1.5 2.2 2.8 2.8L7 6l2 2-1.2 1.4C4.5 9 1 5.5.6 2.2z" fill="var(--text-grey)"/></svg>
      5550142287
      <svg viewBox="0 0 10 10"><rect x="0.5" y="2" width="9" height="6" fill="none" stroke="var(--text-grey)"/><path d="M0.5 2l4.5 3.5L9.5 2" fill="none" stroke="var(--text-grey)"/></svg>
      info@zolvanaworks.example
    </li>
    <li>
      <svg viewBox="0 0 10 10"><circle cx="5" cy="5" r="4.5" fill="var(--text-grey)"/></svg>
      www.zolvanaworks.example
    </li>
  </ul>
</section>

<section class="envelope envelope-back" aria-label="Envelope back">
  <svg class="folds" viewBox="0 0 620 310" width="620" height="310" aria-hidden="true">
    <path d="M0 310 L250 150 Q310 120 370 150 L620 310 Z" fill="var(--paper-shade)" stroke="var(--fold-line)"/>
    <path d="M0 30 L0 300 L230 160 Z" fill="#f0f0f0" stroke="var(--fold-line)"/>
    <path d="M620 30 L620 300 L390 160 Z" fill="#f0f0f0" stroke="var(--fold-line)"/>
  </svg>
  <div class="flap-pattern" role="img" aria-label="Blue geometric pattern on the envelope flap"></div>
  <span class="back-mark"></span>
</section>

</body>
</html>
```